Business Card Design for company

We want new business cards. We'd like something different-- yet still highly professional. Our tagline is Providing leadership, delivering success. Stock photos are ok, as long as they are relevant and look upscale.

Target Market(s)

Architecture/Business Management Consulting/Engineering Consulting

Contact Information for Business Card

dark gray background with pops of blue might be good, but you tell me. You're the designers. Rounded corners might be nice, but again, you tell me.

Font styles to use
Serif
Sans Serif

Colors
3276b5
5c5c5c
9d9d9d
fbfbfb

Requirements
Nice to have
• Something different, but still very professional.

```html
<!DOCTYPE html>
<html lang="en">
<head>
<meta charset="utf-8">
<title>Vantora International – Business Cards</title>
<link href="https://fonts.googleapis.com/css2?family=Roboto:wght@400;500;700&display=swap" rel="stylesheet">
<style>
  :root {
    --brand-blue: #3276b5;
    --band-blue: #2a6099;
    --ink-gray: #5c5c5c;
    --mid-gray: #9d9d9d;
    --paper: #fbfbfb;
    --card-dark: #4a4e56;
    --stage: #2b2b2d;
  }
  * { box-sizing: border-box; margin: 0; padding: 0; }
  html, body {
    width: 1200px; height: 768px; overflow: hidden;
    background: var(--stage);
    font-family: "Roboto", Arial, sans-serif;
  }
  .stage {
    width: 1200px; height: 768px;
    display: flex; align-items: center; justify-content: center; gap: 40px;
  }
  .card {
    position: relative;
    width: 540px; height: 309px;
    border-radius: 6px;
    overflow: hidden;
    box-shadow: 0 10px 30px rgba(0,0,0,.45);
  }

  /* Back */
  .card--back { background: var(--card-dark); color: #fff; }
  .back-name {
    position: absolute; left: 0; right: 0; top: 110px;
    text-align: center; font-weight: 700; font-size: 40px; letter-spacing: 1px;
  }
  .back-tagline {
    position: absolute; left: 0; right: 0; bottom: 40px;
    text-align: center; font-size: 14px; letter-spacing: .5px;
  }

  /* Front */
  .card--front { background: var(--paper); }
  .front-name {
    position: absolute; left: 36px; top: 40px;
    font-weight: 700; font-size: 30px; line-height: 1.1;
    color: var(--brand-blue); letter-spacing: .5px;
  }
  .front-graphics { position: absolute; inset: 0; }
  .holder {
    position: absolute; right: 26px; top: 118px; width: 180px;
    text-align: right; color: #fff;
  }
  .holder-name { font-weight: 700; font-size: 19px; letter-spacing: 1px; }
  .holder-title { font-weight: 500; font-size: 12px; letter-spacing: 1px; margin-top: 2px; }
  .address {
    position: absolute; left: 40px; top: 144px;
    font-size: 13px; line-height: 18px; color: var(--ink-gray);
  }
  .contacts {
    position: absolute; left: 24px; top: 186px; list-style: none;
    font-size: 13px; line-height: 19px; color: var(--ink-gray);
  }
  .contacts li { display: flex; align-items: center; gap: 6px; }
  .contacts svg { width: 11px; height: 11px; fill: var(--band-blue); flex: none; }
</style>
</head>
<body>
<main class="stage">
  <section class="card card--back" aria-label="Card back">
    <div class="back-name">VANTORA INTERNATIONAL</div>
    <p class="back-tagline">Providing leadership, delivering success</p>
  </section>

  <section class="card card--front" aria-label="Card front">
    <svg class="front-graphics" viewBox="0 0 540 309" aria-hidden="true">
      <line x1="0" y1="128" x2="360" y2="128" stroke="var(--brand-blue)" stroke-width="1"/>
      <polygon points="378,108 540,108 540,172 340,172" fill="var(--band-blue)"/>
    </svg>
    <div class="front-name">VANTORA<br>INTERNATIONAL</div>
    <div class="holder">
      <div class="holder-name">DANIEL REYES</div>
      <div class="holder-title">CEO/FOUNDER</div>
    </div>
    <address class="address" style="font-style:normal">
      1420 Alder Ridge Road<br>Juneau, Alaska 99801
    </address>
    <ul class="contacts">
      <li><svg viewBox="0 0 12 12"><path d="M2.5 0.5 4.5 3 3.5 4.5c.8 1.7 2.2 3.1 4 4L9 7.5l2.5 2-1.3 2C5.5 11.5.5 6.5.5 1.8z"/></svg>555 214 0387</li>
      <li><svg viewBox="0 0 12 12"><rect x="3" y="0.5" width="6" height="3.5"/><rect x="0.5" y="4.5" width="11" height="5" rx="1"/><rect x="3" y="8" width="6" height="3.5" fill="#fff" stroke="currentColor"/></svg>555 214 0391</li>
      <li><svg viewBox="0 0 12 12"><rect x="0.5" y="2" width="11" height="8" rx="1"/><path d="M1 2.5 6 6.5 11 2.5" stroke="#fff" fill="none"/></svg>daniel@vantoraintl.com</li>
      <li><svg viewBox="0 0 12 12"><circle cx="6" cy="6" r="5.5"/><path d="M.5 6h11M6 .5c-2.5 3-2.5 8 0 11M6 .5c2.5 3 2.5 8 0 11" stroke="#fff" stroke-width=".8" fill="none"/></svg>www.vantoraintl.com</li>
    </ul>
  </section>
</main>
</body>
</html>
```